We need a business card design, letterhead design and envelope design for our corporate image

We are looking for a corporate business card design, letterhead and envelope design to match the business card design. Logo is done.

```html
<!DOCTYPE html>
<html lang="en">
<head>
<meta charset="utf-8">
<title>Lumacote Business Card</title>
<link href="https://fonts.googleapis.com/css2?family=Open+Sans:ital,wght@0,400;0,600;0,700;1,400;1,700&display=swap" rel="stylesheet">
<style>
  :root {
    --backdrop: #262626;
    --card-white: #ffffff;
    --brand-gray: #6b6c70;
    --brand-yellow: #f9c80e;
    --ink-gray: #5f6064;
    --ink-white: #ffffff;
  }
  * { margin: 0; padding: 0; box-sizing: border-box; }
  html, body {
    width: 1200px; height: 900px; overflow: hidden;
    background: var(--backdrop);
    font-family: "Open Sans", Arial, sans-serif;
  }
  .canvas {
    position: relative; width: 1200px; height: 900px;
    display: flex; flex-direction: column; align-items: center; justify-content: center; gap: 50px;
  }
  .card {
    position: relative; width: 600px; height: 343px; overflow: hidden;
    box-shadow: 0 10px 30px rgba(0,0,0,.45);
  }
  .card-front { background: var(--card-white); }
  .card-back { background: var(--brand-gray); }

  .brand-name { position: absolute; font-weight: 700; letter-spacing: -0.5px; white-space: nowrap; }
  .card-front .brand-name { top: 52px; right: 48px; font-size: 40px; color: var(--ink-gray); }
  .card-back .brand-name {
    top: 50%; left: 50%; transform: translate(-50%, -50%);
    font-size: 66px; color: var(--ink-white);
  }

  .person { position: absolute; left: 34px; top: 122px; }
  .person-name { color: var(--brand-yellow); font-weight: 700; font-style: italic; font-size: 22px; letter-spacing: .3px; text-transform: uppercase; }
  .person-title { color: var(--ink-gray); font-style: italic; font-size: 15px; margin-top: -2px; }

  .divider { position: absolute; left: 0; top: 0; }

  .contacts { position: absolute; left: 34px; top: 196px; list-style: none; }
  .contacts li { display: flex; align-items: center; gap: 8px; color: var(--ink-gray); font-size: 14px; line-height: 21px; }
  .contacts svg { width: 13px; height: 13px; flex: none; }

  .address { position: absolute; right: 34px; top: 224px; text-align: right; color: var(--ink-gray); font-size: 14px; line-height: 20px; font-style: normal; }

  .footer-band { position: absolute; left: 0; bottom: 0; }
  .website { position: absolute; right: 34px; bottom: 8px; color: var(--ink-white); font-size: 14px; }
</style>
</head>
<body>
<main class="canvas">
  <section class="card card-front">
    <p class="brand-name">Lumacote</p>

    <div class="person">
      <p class="person-name">Daniel Reyes</p>
      <p class="person-title">President</p>
    </div>

    <svg class="divider" width="600" height="343" viewBox="0 0 600 343">
      <line x1="34" y1="182" x2="566" y2="214" stroke="var(--brand-yellow)" stroke-width="1.5"/>
    </svg>

    <ul class="contacts">
      <li>
        <svg viewBox="0 0 16 16"><path d="M3.5 1.5l3 3-1.6 1.7a9 9 0 0 0 4.9 4.9L11.5 9.5l3 3-2 2C6.5 14 2 9.5 1.5 3.5z" fill="var(--brand-yellow)"/></svg>
        555-014-2387
      </li>
      <li>
        <svg viewBox="0 0 16 16"><rect x="4" y="1" width="8" height="14" rx="1.5" fill="none" stroke="var(--brand-yellow)" stroke-width="1.6"/></svg>
        555-014-2387
      </li>
      <li>
        <svg viewBox="0 0 16 16"><rect x="1" y="3" width="14" height="10" fill="var(--brand-yellow)"/><path d="M1 3l7 6 7-6" fill="none" stroke="#fff" stroke-width="1.2"/></svg>
        dreyes@lumacote.com
      </li>
    </ul>

    <address class="address">
      1870 Harbor View Lane<br>Seacliff CA 90210
    </address>

    <svg class="footer-band" width="600" height="70" viewBox="0 0 600 70">
      <path d="M0 28 L300 28 C318 28 322 36 320 40 L0 40 Z" fill="var(--brand-yellow)"/>
      <path d="M0 40 L310 40 C330 40 336 30 356 30 L600 30 L600 70 L0 70 Z" fill="var(--brand-gray)"/>
    </svg>
    <p class="website">www.lumacote.com</p>
  </section>

  <section class="card card-back">
    <p class="brand-name">Lumacote</p>
  </section>
</main>
</body>
</html>
```